Accounting firm needs a flyer "Brevora Group".. many job after this Stationary, business card

We need a flyer for a new company based in Melbourne Australia. We are group of young professionals who intend to provide various accounting services, taxation, finance, bookkeeping and payroll, Business service service advisory and management consulting.The main task of the firm is to provide accounting and taxation services. we then use our associates/referral partners to assist client with their legal, migration, finance needs.

We would like to see designs that match our logo, business card and letter head which I have uploaded along with this. I have also uploaded some of our website contents that might be used in flyers.
My favorite colors are: Blue (navy and royal blue), Teal (blue green), Turquoise, purple(orchid, lavender, plum).

Our brand:
Brevora Group
Where counsel runs deeper

Our mission:
To group the professionals in house, Where counsel runs deeper and turn into better business for our people, for our clients and four our communities.

We like our logo, however we are still not sure about our business card. So if we are open to work with someone who works with flyers and business card at the same time .

Target Market(s)

Individual and business client in Australia

Industry/Entity Type

Finance And Accounting

Colors
0255a3
3176b5
0493ce
33a6d7
886aae
b768aa
00a990
33b8a4

Requirements
Must have
• Brevora Group logo
• Liability limited by a scheme approved under the professional standards legislation
• Our motto: Brevora Group where counsel runs deeper
• Short description of our services:
• • Bookkeeping & Payroll
• • Finance & Capital Raising
• • Taxation, Accounting and compliances
• • Business service and advisory
• • Migration
• • ASIC and Corporate Secretarial
• • Business law and legal services
• About us
• BREVORA aim to be more than just an accounting firm. We support our clients to help them achieve their personal and business goals by offering a fully integrated advisory service, helping clients to build wealth and protect their assets.We will bring together the relevant professionals across a number of specialties and locations; providing a responsive, personalised solution.
• Our mission: To group the professionals in house, Where counsel runs deeper and turn into better business for our people, for our clients and four our communities.
Nice to have
• Tax agent logo
• FLT logo

```html
<!DOCTYPE html>
<html lang="en">
<head>
<meta charset="utf-8">
<title>Brevora Group – Business Card</title>
<link href="https://fonts.googleapis.com/css2?family=Lato:wght@300;400;700;900&display=swap" rel="stylesheet">
<style>
  :root{
    --bg:#e9eaec;
    --card-white:#ffffff;
    --navy:#1b2a5c;
    --navy-deep:#0c1f66;
    --royal:#1747b0;
    --blue:#1587d2;
    --cyan:#22b4ea;
    --ink:#1e2a55;
    --muted:#8a97c0;
    --icon:#333a45;
  }
  *{margin:0;padding:0;box-sizing:border-box}
  html,body{width:1200px;height:962px;overflow:hidden}
  body{background:var(--bg);font-family:'Lato',sans-serif;position:relative}

  .card{position:absolute;width:560px;height:320px;border-radius:4px;overflow:hidden;
        box-shadow:0 12px 28px rgba(0,0,0,.16)}

  /* front face */
  .card--front{left:70px;top:120px;background:var(--card-white)}
  .holder{position:absolute;left:200px;top:78px;white-space:nowrap}
  .holder__name{font-size:50px;color:var(--ink);line-height:1}
  .holder__first{font-weight:900}
  .holder__last{font-weight:300;letter-spacing:1px}
  .holder__role{font-size:18px;font-weight:300;color:var(--muted);letter-spacing:1px;margin:4px 0 0 138px}

  .contact{position:absolute;bottom:0;color:#fff;text-align:center;line-height:1.45}
  .contact--address{left:0;width:200px;height:100px;background:var(--blue);font-size:14px;padding-top:36px}
  .contact--phone{left:200px;width:145px;height:135px;background:var(--cyan);font-size:16px;padding-top:38px}
  .contact--web{left:345px;width:215px;height:170px;background:var(--navy);font-size:13.5px;padding-top:52px}

  .contact-icon{position:absolute;width:18px;height:18px}
  .contact-icon--home{left:91px;top:184px}
  .contact-icon--phone{left:264px;top:150px}
  .contact-icon--globe{left:444px;top:114px}

  /* back face */
  .card--back{left:570px;top:470px;
     background:radial-gradient(ellipse at 55% 45%,var(--royal) 0%,var(--navy-deep) 72%)}
  .brand{position:absolute;left:0;right:0;top:62px;display:flex;flex-direction:column;align-items:center}
  .brand__dot{width:118px;height:118px;border-radius:50%;background:var(--blue)}
  .brand__name{margin-top:14px;font-size:40px;font-weight:900;color:#fff;letter-spacing:3px;line-height:1}
  .brand__tagline{margin-top:8px;font-size:11px;font-weight:400;color:#fff;letter-spacing:2.5px}
</style>
</head>
<body>

<section class="card card--front" aria-label="Business card front">
  <div class="holder">
    <p class="holder__name"><span class="holder__first">Lena</span> <span class="holder__last">Maris</span></p>
    <p class="holder__role">Director</p>
  </div>

  <svg class="contact-icon contact-icon--home" viewBox="0 0 20 20" aria-hidden="true">
    <path d="M10 3 2 10h2.5v7h4v-4.5h3V17h4v-7H18z" fill="var(--icon)"/>
  </svg>
  <svg class="contact-icon contact-icon--phone" viewBox="0 0 20 20" aria-hidden="true">
    <path d="M3 8c0-3 3-4 7-4s7 1 7 4l-3 1-1-2H7L6 9z" fill="var(--icon)"/>
    <rect x="5" y="10" width="10" height="6" rx="1.5" fill="var(--icon)"/>
  </svg>
  <svg class="contact-icon contact-icon--globe" viewBox="0 0 20 20" aria-hidden="true">
    <g fill="none" stroke="var(--icon)" stroke-width="1.4">
      <circle cx="10" cy="10" r="8"/><ellipse cx="10" cy="10" rx="3.5" ry="8"/>
      <path d="M2 10h16M3.5 6h13M3.5 14h13"/>
    </g>
  </svg>

  <div class="contact contact--address">Level 5 22 Harbour Lane<br>Melbourne Vic 3000</div>
  <div class="contact contact--phone">0412 738 250</div>
  <div class="contact contact--web">lena@brevora.com.au<br>www.brevora.com.au</div>
</section>

<section class="card card--back" aria-label="Business card back">
  <div class="brand">
    <span class="brand__dot" aria-hidden="true"></span>
    <span class="brand__name">BREVORA</span>
    <p class="brand__tagline">TAX &amp; BUSINESS ADVISORS</p>
  </div>
</section>

</body>
</html>
```